Business Card Design for DMV business in Las Vegas, NV - (Very open to design ideas and colors)

We are looking for a business card design for a new company in Las Vegas, NV called Quickline Tag Services. This company is here to give the general public the option of using our services, for a fee, instead of the customer sitting and waiting at a Silverpine Motor Bureau office for 3-6 hours on average. Our business will process vehicle registrations, titles, plates, handicap placards, temporary moving permits, etc. in a fraction of the time compared to the DMV's standard wait times (3-6 hours) hence our business name Quickline Tag SERVICES. Our business will be capable of handling just about any DMV related issue and this will keep our customers happier if our customer never has to show up to the DMV and we do all the work for them. I am very open to design ideas and colors for the business card. One thing that I am looking for is something that catches the eye fast but conveys the message about our business being able to expedite a customer's needs quickly and efficiently. You may modify the wording to say Quickline Tag Services or make SERVICES capitalized. I look forward to reviewing your design ideas. If you want to get ideas about the Silverpine Motor Bureau please visit www.spmotorbureau.org. This is the Silverpine Motor Bureau's official website.
Business
Quickline Tag Services, LLCRyan Steeps - OwnerEmail - NevadaDMVExpress@gmail.comWebsite - NevadaDMVExpress.comPhone # 702-555-0147

```html
<!DOCTYPE html>
<html lang="en">
<head>
<meta charset="utf-8">
<title>Quickline Tag Services – Business Cards</title>
<link href="https://fonts.googleapis.com/css2?family=Marcellus&family=Open+Sans:wght@400;600;700&display=swap" rel="stylesheet">
<style>
  :root {
    --backdrop: #3a322d;
    --card: #0d0d0e;
    --card-glow: #1b1b1d;
    --brand-red: #c8202a;
    --text-white: #f2f2f2;
    --text-soft: #d6d6d6;
    --divider: #3a3a3c;
  }
  * { box-sizing: border-box; margin: 0; padding: 0; }
  html, body {
    width: 1200px;
    height: 844px;
    overflow: hidden;
    background: var(--backdrop);
    font-family: "Open Sans", Arial, sans-serif;
  }
  .stage {
    width: 1200px;
    height: 844px;
    display: flex;
    align-items: center;
    justify-content: center;
    gap: 40px;
  }
  .business-card {
    position: relative;
    width: 545px;
    height: 312px;
    background: radial-gradient(ellipse at 60% 40%, var(--card-glow) 0%, var(--card) 70%);
    box-shadow: 0 14px 32px rgba(0,0,0,0.45);
    flex: none;
  }
  .brand {
    position: absolute;
    display: flex;
    align-items: center;
    gap: 16px;
  }
  .card-front .brand { left: 62px; top: 70px; }
  .card-back .brand { left: 100px; top: 62px; }
  .brand-square {
    width: 86px;
    height: 86px;
    background: var(--brand-red);
    flex: none;
  }
  .brand-name {
    font-family: "Marcellus", Georgia, serif;
    font-weight: 400;
    color: var(--text-white);
    line-height: 1;
    margin-top: -14px;
  }
  .brand-name .line-top { display: block; font-size: 27px; letter-spacing: 0.5px; }
  .brand-name .line-bottom { display: block; font-size: 41px; letter-spacing: 1px; margin-top: 2px; }

  .person-name {
    color: var(--brand-red);
    font-weight: 600;
    font-size: 18px;
    line-height: 1.1;
  }
  .person-role {
    color: var(--text-soft);
    font-size: 12px;
    margin-top: 1px;
  }
  .card-front .person {
    position: absolute;
    right: 318px;
    top: 200px;
    text-align: right;
  }
  .card-front .divider {
    position: absolute;
    left: 240px;
    top: 172px;
    width: 1px;
    height: 88px;
    background: var(--divider);
  }
  .contact-list {
    list-style: none;
  }
  .card-front .contact-list {
    position: absolute;
    left: 254px;
    top: 178px;
  }
  .contact-item {
    display: flex;
    align-items: center;
    gap: 7px;
    color: var(--text-white);
    font-size: 13px;
    line-height: 1;
    margin-bottom: 9px;
  }
  .contact-icon {
    width: 15px;
    height: 15px;
    flex: none;
  }
  .card-back .person {
    position: absolute;
    left: 250px;
    top: 170px;
  }
  .card-back .contact-list {
    position: absolute;
    left: 262px;
    top: 222px;
  }
</style>
</head>
<body>
<main class="stage">
  <section class="business-card card-front" aria-label="Quickline Tag Services business card, front">
    <div class="brand">
      <div class="brand-square" aria-hidden="true"></div>
      <h1 class="brand-name">
        <span class="line-top">Quickline Tag</span>
        <span class="line-bottom">SERVICES</span>
      </h1>
    </div>

    <div class="person">
      <p class="person-name">Colin Marwick</p>
      <p class="person-role">Owner</p>
    </div>

    <div class="divider" aria-hidden="true"></div>

    <ul class="contact-list">
      <li class="contact-item">
        <svg class="contact-icon" viewBox="0 0 22 22" aria-hidden="true">
          <rect width="22" height="22" rx="3" fill="var(--brand-red)"/>
          <path d="M5 8c0-2 1.5-3 3-3h6c1.5 0 3 1 3 3v1h-3V8H8v1H5z" fill="#fff"/>
          <rect x="6" y="10" width="10" height="7" rx="1.5" fill="#fff"/>
        </svg>
        <span>702-555-0147</span>
      </li>
      <li class="contact-item">
        <svg class="contact-icon" viewBox="0 0 22 22" aria-hidden="true">
          <rect width="22" height="22" rx="3" fill="var(--brand-red)"/>
          <rect x="4.5" y="6.5" width="13" height="9" fill="none" stroke="#fff" stroke-width="1.6"/>
          <path d="M4.5 6.5l6.5 5 6.5-5" fill="none" stroke="#fff" stroke-width="1.6"/>
        </svg>
        <span>QuicklineTagServices@tagmailbox.net</span>
      </li>
      <li class="contact-item">
        <svg class="contact-icon" viewBox="0 0 22 22" aria-hidden="true">
          <rect width="22" height="22" rx="3" fill="var(--brand-red)"/>
          <rect x="4" y="9" width="8" height="5" rx="2.5" fill="none" stroke="#fff" stroke-width="1.6" transform="rotate(-45 8 11.5)"/>
          <rect x="10" y="8" width="8" height="5" rx="2.5" fill="none" stroke="#fff" stroke-width="1.6" transform="rotate(-45 14 10.5)"/>
        </svg>
        <span>QuicklineTagServices.com</span>
      </li>
    </ul>
  </section>

  <section class="business-card card-back" aria-label="Quickline Tag Services business card, back">
    <div class="brand">
      <div class="brand-square" aria-hidden="true"></div>
      <p class="brand-name">
        <span class="line-top">Quickline Tag</span>
        <span class="line-bottom">SERVICES</span>
      </p>
    </div>

    <div class="person">
      <p class="person-name">Colin Marwick</p>
      <p class="person-role">Owner</p>
    </div>

    <ul class="contact-list">
      <li class="contact-item">
        <svg class="contact-icon" viewBox="0 0 22 22" aria-hidden="true">
          <rect width="22" height="22" rx="3" fill="var(--brand-red)"/>
          <path d="M5 8c0-2 1.5-3 3-3h6c1.5 0 3 1 3 3v1h-3V8H8v1H5z" fill="#fff"/>
          <rect x="6" y="10" width="10" height="7" rx="1.5" fill="#fff"/>
        </svg>
        <span>702-555-0147</span>
      </li>
    </ul>
  </section>
</main>
</body>
</html>
```